Zvo Klinieken website for a maxillofacial surgery clinic

It's a website for a clinic for maxillofacial surgery in WordPress . The website doesn't need to be complicated but has to look professional. It needs to be in Dutch so i can give the texts. Similar websites are www.tandartsenpraktijkveldorm.nl or www.pbtspecialisten.nl. Pages would be sort of similar to https://hetcentrumvoorgezichtszorg.nl/ or https://wervelmondclinics.nl/. Those lasts are maxillofacial surgery clinic websites, but there are little more extensive.
I uploaded the logo. If this is not the proper quality i can upload the eps. Logo was made through pixelforum.

Target Market(s)

Patients who can find me and see information about the clinic

Industry/Entity Type

Healthcare

Coding

Coded - Design and coding required

Number of Pages Required

5+ page

Font styles to use
Other font styles liked:
• Something standard professional

Colors
0054AA
0677BA
7BADD7
CADEEF
E8F1F8

Requirements
Nice to have
• Something in line with the logo. I prefer a little dark like the darker logos but I'm not sure if that's professional. Logos bkvzo and rlpw are instances i'm registered to so they will have to be on the website too but small somewhere.

```html
<!DOCTYPE html>
<html lang="nl">
<head>
<meta charset="utf-8">
<title>Zvo Klinieken – Kaakchirurgie</title>
<link href="https://fonts.googleapis.com/css2?family=Montserrat:wght@400;500;600;700;800&display=swap" rel="stylesheet">
<style>
:root{
  --accent:#2ea3dc;
  --accent-band:#33aae0;
  --slate:#6f84a8;
  --slate-band:#7d90b3;
  --ink:#1d1d1f;
  --text:#333;
  --muted:#8a8a8a;
  --footer:#2b2f36;
  --footer-line:#454a52;
  --white:#fff;
}
*{margin:0;padding:0;box-sizing:border-box}
html,body{width:1200px;height:4095px;overflow:hidden}
body{font-family:'Montserrat',sans-serif;color:var(--text);background:var(--white);position:relative}
.abs{position:absolute}
.ph{position:absolute}
/* top bar */
.topbar{top:0;left:0;width:1200px;height:54px;background:var(--slate);color:#fff;font-size:13px}
.topbar .item{position:absolute;top:19px;display:flex;align-items:center;gap:12px}
/* nav */
.nav{top:54px;left:0;width:1200px;height:86px;background:#fff}
.brand{position:absolute;left:122px;top:33px;display:flex;align-items:center;gap:7px;font-weight:700;font-size:15px;color:var(--accent);white-space:nowrap}
.brand .dot{width:16px;height:16px;border-radius:50%;background:var(--accent)}
.menu{position:absolute;top:32px;left:292px;display:flex;gap:41px;font-weight:600;font-size:17px;color:var(--ink)}
.btn{display:inline-block;background:var(--accent);color:#fff;font-weight:700;text-transform:uppercase;text-align:center}
.nav .btn{position:absolute;left:982px;top:20px;width:100px;height:44px;line-height:44px;font-size:17px}
/* hero */
.hero{top:140px;left:0;width:1200px;height:610px;overflow:hidden}
.hero-photo{left:0;top:0;width:1200px;height:610px;background:linear-gradient(100deg,#e6ecf2 0%,#dbe3ea 35%,#c9d6e4 60%,#aec3da 100%)}
.hero h3{position:absolute;left:119px;top:104px;font-size:24px;font-weight:600;color:var(--ink)}
.hero h1{position:absolute;left:122px;top:150px;font-size:58px;font-weight:700;color:var(--accent);letter-spacing:1px}
.hero p{position:absolute;left:126px;top:233px;width:445px;font-size:15px;font-weight:700;line-height:24px;color:var(--ink)}
.hero .btn{position:absolute;left:125px;top:322px;width:101px;height:43px;line-height:43px;font-size:16px}
/* headings */
.h2{font-size:35px;font-weight:800;color:var(--ink)}
.h2 span{color:var(--accent)}
/* about */
.about-h{left:111px;top:752px}
.about-sub{left:116px;top:818px;width:470px;font-size:17px;font-weight:600;line-height:28px;color:var(--ink)}
.about-p{left:118px;top:888px;width:432px;font-size:14px;line-height:24px}
.about-btn{left:116px;top:1034px;width:148px;height:45px;line-height:45px;font-size:17px}
/* services */
.services{top:1184px;left:0;width:1200px;height:667px;background:linear-gradient(110deg,#7486ab,#8597b9 55%,#7a8db1)}
.services h2{position:absolute;top:40px;width:1200px;text-align:center;font-size:36px;font-weight:800;color:#fff}
.services .lead{position:absolute;left:250px;top:110px;width:700px;text-align:center;font-size:17px;font-weight:700;line-height:34px;color:#fff}
.card{position:absolute;top:256px;width:297px;height:352px;background:#fff;box-shadow:0 4px 12px rgba(0,0,0,.15)}
.card .img{position:absolute;left:0;top:0;width:100%;height:184px}
.card h4{position:absolute;left:9px;top:210px;font-size:17px;font-weight:700;color:var(--ink)}
.card p{position:absolute;left:11px;top:250px;width:280px;font-size:15px;line-height:27px}
/* about 2 */
.about2-h{left:111px;top:1933px}
.about2-sub{left:116px;top:1995px;font-size:17px;font-weight:700;color:var(--ink)}
.about2-p{left:118px;width:530px;font-size:16px;line-height:26px;color:var(--ink)}
/* testimonials */
.testi{top:2339px;left:0;width:1200px;height:508px;background:linear-gradient(120deg,#37a9df,#5bb9e6 50%,#3aa6dc)}
.testi h2{position:absolute;top:62px;width:1200px;text-align:center;font-size:36px;font-weight:800;color:#fff}
.quote{position:absolute;top:156px;width:448px;height:184px;border:2px solid #fff}
.quote .mark{position:absolute;left:16px;top:8px;font-size:46px;font-weight:800;color:#fff;line-height:1}
.quote p{position:absolute;left:55px;top:26px;width:380px;font-size:16px;line-height:32px;color:#fff}
.quote svg{position:absolute;left:46px;top:180px}
.avatar{position:absolute;top:376px;width:80px;height:80px;border-radius:50%;background:linear-gradient(#e9eef2,#b9c6d1);border:2px solid #fff}
.who{position:absolute;top:396px;color:#fff}
.who b{display:block;font-size:17px;font-weight:700}
.who span{display:block;margin-top:12px;font-size:16px}
/* team */
.team-h{left:111px;top:2925px}
.member{position:absolute;top:3011px;width:255px}
.member .img{width:255px;height:266px}
.member b{display:block;margin-top:18px;text-align:center;font-size:20px;font-weight:700;color:var(--ink)}
.member span{display:block;margin-top:10px;padding-left:68px;font-size:16px;font-weight:500;color:var(--muted)}
/* cta */
.cta{top:3429px;left:0;width:1200px;height:237px;background:var(--accent-band)}
.cta p{position:absolute;left:130px;top:102px;font-size:21px;font-weight:700;color:#fff;white-space:nowrap}
/* footer */
.footer{top:3666px;left:0;width:1200px;height:429px;background:var(--footer);color:#fff}
.footer .fbrand{position:absolute;left:140px;top:80px;display:flex;align-items:center;gap:12px;font-size:34px;font-weight:700;color:var(--accent);white-space:nowrap}
.footer .fbrand .dot{width:30px;height:30px;border-radius:50%;background:var(--accent)}
.footer .fp{position:absolute;left:129px;top:185px;width:440px;font-size:15px;line-height:33px}
.social{position:absolute;top:291px;width:28px;height:28px;border-radius:50%;background:#fff}
.footer h5{position:absolute;top:82px;font-size:22px;font-weight:700}
.links{position:absolute;left:625px;top:134px;list-style:none;font-size:15px}
.links li{height:32.6px}
.crow{position:absolute;left:842px;display:flex;align-items:center;gap:16px;font-size:16px}
.footer .rule{position:absolute;left:0;top:351px;width:1200px;height:1px;background:var(--footer-line)}
.footer .copy{position:absolute;top:370px;width:1200px;text-align:center;font-size:16px}
</style>
</head>
<body>

<header class="abs topbar">
  <div class="item" style="left:128px">
    <svg width="18" height="20" viewBox="0 0 18 20"><path d="M9 1a6 6 0 0 0-6 6c0 4.5 6 10 6 10s6-5.5 6-10a6 6 0 0 0-6-6z" fill="none" stroke="#fff" stroke-width="2"/><circle cx="9" cy="7" r="2" fill="#fff"/></svg>
    <span>Zvo Klinieken</span>
  </div>
  <div class="item" style="left:478px">
    <svg width="20" height="20" viewBox="0 0 20 20"><path d="M4 1l4 4-2 3c1.5 3 3 4.5 6 6l3-2 4 4-3 3C8 18 2 12 1 4z" fill="#fff"/></svg>
    <span>+31 20 555 0142</span>
  </div>
  <div class="item" style="left:852px">
    <svg width="22" height="16" viewBox="0 0 22 16"><rect x="1" y="1" width="20" height="14" fill="none" stroke="#fff" stroke-width="2"/><path d="M1 1l10 8 10-8" fill="none" stroke="#fff" stroke-width="2"/></svg>
    <span>info@zvoklinieken.nl</span>
  </div>
</header>

<nav class="abs nav">
  <div class="brand"><span class="dot"></span>Zvo Klinieken</div>
  <div class="menu"><span>Huis</span><span>Overons</span><span>Diensten</span><span>Team</span><span>Getuigenissen</span><span>Contact</span></div>
  <span class="btn">Begin</span>
</nav>

<section class="abs hero">
  <div class="ph hero-photo" role="img" aria-label="Foto: glimlachende patiënte in de tandartsstoel met tandarts"></div>
  <svg class="abs" style="left:0;top:0" width="1200" height="610" viewBox="0 0 1200 610">
    <path d="M0 560 C250 520 420 430 620 440 C820 450 1000 430 1200 580 L1200 610 L0 610Z" fill="#fff"/>
    <path d="M360 490 C520 430 700 420 800 440 C980 460 1100 520 1200 600 L1200 560 C1100 470 980 420 800 415 C660 410 500 430 360 490Z" fill="var(--accent)"/>
    <rect x="157" y="457" width="210" height="70" fill="#2f3640"/>
    <path d="M157 560 C250 540 320 510 367 490 L367 610 L157 610Z" fill="#fff"/>
  </svg>
  <h3>welkom bij</h3>
  <h1>ZVO CLINIC</h1>
  <p>Lorem ipsum dolor sit amet, consectetur adipiscing elit, sed do eiusmod tempor incididunt ut labore et dolore magna aliqua.</p>
  <span class="btn">Begin</span>
</section>

<h2 class="abs h2 about-h">Over onze <span>kliniek</span></h2>
<p class="abs about-sub">Maar om te laten zien waar al deze geboren dwaling vandaan komt van degenen die</p>
<p class="abs about-p">Lorem ipsum dolor sit amet, consectetur adipiscing elit, sed do eiusmod tempor incididunt ut labore et dolore magna aliqua. Ut enim ad minim veniam, quis nostrud exercitation ullamco laboris nisi ut aliquip ex ea commodo consequat.</p>
<span class="abs btn about-btn">Lees meer</span>
<div class="ph" style="left:628px;top:744px;width:230px;height:333px;background:linear-gradient(160deg,#dfe3e8,#e88a4a 55%,#d9a889)" role="img" aria-label="Foto: patiënte met beschermbril tijdens behandeling"></div>
<div class="ph" style="left:864px;top:742px;width:218px;height:164px;background:linear-gradient(135deg,#c9dde6,#e7d6cf)" role="img" aria-label="Foto: glimlach met witte tanden"></div>
<div class="ph" style="left:864px;top:912px;width:218px;height:165px;background:linear-gradient(135deg,#6e85b0,#dfe6f0 70%)" role="img" aria-label="Foto: model van een kies met tandheelkundig instrument"></div>

<section class="abs services">
  <h2>Onze diensten</h2>
  <p class="lead">Lorem ipsum dolor sit amet, consectetur adipiscing elit, sed do eiusmod tempor incididunt ut labore et dolore magna aliqua. Ut enim ad minim veniam, quis nostrud exercitation ullamco</p>
  <div class="card" style="left:119px">
    <div class="img" style="background:linear-gradient(135deg,#cfd8e0,#e6e9ec 60%,#c7a882)" role="img" aria-label="Foto: arts bekijkt röntgenfoto met patiënt"></div>
    <h4>KAAKCHIRURGIE</h4>
    <p>Lorem ipsum dolor sit amet, consectetur adipiscing elit, sed do eiusmod tempor incididunt ut</p>
  </div>
  <div class="card" style="left:448px">
    <div class="img" style="background:linear-gradient(180deg,#e0344d,#f0566a 70%,#e7c7b5)" role="img" aria-label="Illustratie: doorsnede van een kies op rode achtergrond"></div>
    <h4>VERWIJSPRAKTIJK</h4>
    <p>Lorem ipsum dolor sit amet, consectetur adipiscing elit, sed do eiusmod tempor incididunt ut</p>
  </div>
  <div class="card" style="left:779px">
    <div class="img" style="background:linear-gradient(180deg,#e9e3dc,#d68c94 60%,#9c9ba0)" role="img" aria-label="Illustratie: tandimplantaten in het kaakbot"></div>
    <h4>VERWIJSPRAKTIJK</h4>
    <p>Lorem ipsum dolor sit amet, consectetur adipiscing elit, sed do eiusmod tempor incididunt ut</p>
  </div>
</section>

<h2 class="abs h2 about2-h">Over onze <span>kliniek</span></h2>
<p class="abs about2-sub">Tanden bleken</p>
<p class="abs about2-p" style="top:2038px">Lorem ipsum dolor sit amet, consectetur adipiscing elit, sed do eiusmod tempor incididunt ut labore et dolore magna aliqua. Ut enim ad minim veniam, quis nostrud exercitation ullamco laboris nisi ut aliquip ex ea commodo consequat</p>
<p class="abs about2-p" style="top:2153px">Duis aute irure dolor in reprehenderit in voluptate velit esse cillum dolore eu fugiat nulla pariatur. Excepteur sint occaecat cupidatat non proident, sunt in culpa qui officia deserunt mollit anim id est laborum."</p>
<div class="ph" style="left:691px;top:2007px;width:186px;height:261px;background:linear-gradient(180deg,#e4c1a8,#c9856f 55%,#e0b79c)" role="img" aria-label="Foto: glimlach met verkleurde tanden vóór bleken"></div>
<div class="ph" style="left:883px;top:1935px;width:186px;height:263px;background:linear-gradient(180deg,#e8c9b2,#cf8a78 55%,#ebc4aa)" role="img" aria-label="Foto: glimlach met witte tanden na bleken"></div>

<section class="abs testi">
  <h2>Wat onze patiënten zeggen</h2>
  <div class="quote" style="left:140px">
    <span class="mark">“</span>
    <p>Lorem ipsum dolor sit amet, consectetur adipiscing elit, sed do eiusmod tempor incididunt ut labore et dolore magna aliquaUt enim ad minim veniam, quis nostrud</p>
    <svg width="60" height="30" viewBox="0 0 60 30"><path d="M0 1 L14 26 L58 1" fill="var(--accent)" stroke="#fff" stroke-width="2"/></svg>
  </div>
  <div class="quote" style="left:609px">
    <span class="mark">“</span>
    <p>Lorem ipsum dolor sit amet, consectetur adipiscing elit, sed do eiusmod tempor incididunt ut labore et dolore magna aliquaUt enim ad minim veniam, quis nostrud</p>
    <svg width="60" height="30" viewBox="0 0 60 30"><path d="M0 1 L14 26 L58 1" fill="#4fb3e3" stroke="#fff" stroke-width="2"/></svg>
  </div>
  <div class="avatar" style="left:151px" role="img" aria-label="Portretfoto van patiënte"></div>
  <div class="who" style="left:248px"><b>ANNA DE WIT</b><span>California</span></div>
  <div class="avatar" style="left:619px" role="img" aria-label="Portretfoto van patiënt"></div>
  <div class="who" style="left:716px"><b>PIETER JANSEN</b><span>London</span></div>
</section>

<h2 class="abs h2 team-h">Ons <span>Team</span></h2>
<div class="member" style="left:60px">
  <div class="ph img" style="position:static;background:linear-gradient(180deg,#e3e7ea,#f2f3f4 60%,#d9dde0)" role="img" aria-label="Portretfoto van Dr. Lotte Verbeek"></div>
  <b>Dr. Lotte Verbeek</b><span>Sr DMD</span>
</div>
<div class="member" style="left:331px">
  <div class="ph img" style="position:static;background:linear-gradient(180deg,#8fa3ad,#7fb3d6 65%,#5f9bc7)" role="img" aria-label="Portretfoto van Dr. Bram Hoekstra"></div>
  <b>Dr. Bram Hoekstra</b><span>Sr Surgon</span>
</div>
<div class="member" style="left:601px">
  <div class="ph img" style="position:static;background:linear-gradient(180deg,#9fb0b3,#e6e9ea 65%,#c9d0d2)" role="img" aria-label="Portretfoto van Dr. Joris Dekker"></div>
  <b>Dr. Joris Dekker</b><span>Sr DMD</span>
</div>
<div class="member" style="left:871px">
  <div class="ph img" style="position:static;background:linear-gradient(180deg,#e7ecef,#f3f5f6 55%,#8fcfc6)" role="img" aria-label="Portretfoto van Dr. Femke Smit"></div>
  <b>Dr. Femke Smit</b><span>Sr Surgon</span>
</div>

<section class="abs cta">
  <p>Neem vandaag nog contact met ons op (020) 555 0199</p>
</section>
<div class="ph" style="left:820px;top:3385px;width:250px;height:281px;background:linear-gradient(180deg,#e9edf0,#f7f8f9 50%,#dfe5ea);border-radius:120px 120px 0 0" role="img" aria-label="Foto: glimlachende tandarts in witte jas"></div>

<footer class="abs footer">
  <div class="fbrand"><span class="dot"></span>Zvo Klinieken</div>
  <p class="fp">Lorem ipsum dolor sit amet, consectetur adipiscing elit, sed do eiusmod tempor incididunt ut labore et dolore magna aliqua.</p>
  <span class="social" style="left:129px"></span>
  <span class="social" style="left:173px"></span>
  <span class="social" style="left:216px"></span>
  <h5 style="left:623px">Snelle links</h5>
  <ul class="links"><li>huis</li><li>over ons</li><li>Diensten</li><li>Team</li><li>Getuigenissen</li><li>Contact</li></ul>
  <h5 style="left:842px">Contact</h5>
  <div class="crow" style="top:142px">
    <svg width="18" height="20" viewBox="0 0 18 20"><path d="M9 1a6 6 0 0 0-6 6c0 4.5 6 10 6 10s6-5.5 6-10a6 6 0 0 0-6-6z" fill="none" stroke="#fff" stroke-width="2"/><circle cx="9" cy="7" r="2" fill="#fff"/></svg>
    <span>Zvo Klinieken</span>
  </div>
  <div class="crow" style="top:196px">
    <svg width="20" height="20" viewBox="0 0 20 20"><path d="M4 1l4 4-2 3c1.5 3 3 4.5 6 6l3-2 4 4-3 3C8 18 2 12 1 4z" fill="#fff"/></svg>
    <span>+31 20 555 0142</span>
  </div>
  <div class="crow" style="top:249px">
    <svg width="22" height="16" viewBox="0 0 22 16"><rect x="1" y="1" width="20" height="14" fill="none" stroke="#fff" stroke-width="2"/><path d="M1 1l10 8 10-8" fill="none" stroke="#fff" stroke-width="2"/></svg>
    <span>info@zvoklinieken.nl</span>
  </div>
  <div class="rule"></div>
  <p class="copy">Copyrights ZVO CLINIC @.com Alle rechten voorbehouden</p>
</footer>

</body>
</html>
```